2 sided flyer for Insurance Servics

Would like a flyer that talks about who we are, our services, and our process. Attaching relevant information, as well as our Logo and other logos for a few larger insurance carriers that we have access to.

Target Market(s)

Financial Advisors and Insurance Agents

Industry/Entity Type

Finance and Insurance

Colors
0054AA
0677BA
7BADD7
CADEEF
E8F1F8
F0912C
F2A743
F7CA91
FBE8D2
FDF5EE

Requirements
Must have
• Lists, bullet points, pictures, and logos uploaded

```html
<!DOCTYPE html>
<html lang="en">
<head>
<meta charset="utf-8">
<title>Harborline Coverage Group – Services Flyer</title>
<link rel="stylesheet" href="https://fonts.googleapis.com/css2?family=Bebas+Neue&family=Poppins:wght@400;600;700;800&display=swap">
<style>
  :root {
    --blue-bright: #3f94f2;
    --blue-deep: #1657d4;
    --blue-sky: #66c4ff;
    --blue-pale: #7fd6ff;
    --navy: #0d1b33;
    --teal-dark: #1b3640;
    --ink: #1b1b1f;
    --white: #ffffff;
  }
  * { box-sizing: border-box; margin: 0; padding: 0; }
  html, body { width: 848px; height: 1200px; overflow: hidden; background: var(--white); }
  body { position: relative; font-family: "Poppins", sans-serif; color: var(--ink); }
  .abs { position: absolute; }

  .brand-card {
    left: 42px; top: 0; width: 208px; height: 268px;
    border-radius: 0 0 40px 40px;
    background: linear-gradient(180deg, #3f99ff 0%, #8ec6ff 40%, #ffffff 62%);
    box-shadow: 0 6px 14px rgba(0,0,0,0.08);
  }
  .brand-name {
    left: 62px; top: 183px; width: 170px;
    display: flex; align-items: center; gap: 8px;
  }
  .brand-name .mark { width: 26px; height: 26px; background: var(--blue-deep); flex: none; }
  .brand-name span { font-weight: 800; font-size: 13px; line-height: 15px; color: var(--blue-deep); }

  .photo-top {
    left: 416px; top: 0; width: 432px; height: 161px;
    background: radial-gradient(ellipse at 60% 55%, #4f7f86 0%, #284a52 45%, var(--teal-dark) 100%);
  }
  .headline-box {
    left: 315px; top: 161px; width: 533px; height: 210px;
    background: linear-gradient(90deg, #3d9bff 0%, #5db9ff 60%, #6fcbff 100%);
  }
  .headline {
    left: 338px; top: 181px; width: 500px;
    font-family: "Bebas Neue", sans-serif; font-size: 57px; line-height: 54px;
    color: var(--white); letter-spacing: 0.5px;
  }
  .fold { left: 315px; top: 370px; }
  .photo-main {
    left: 416px; top: 370px; width: 432px; height: 399px;
    border-radius: 0 0 0 95px;
    background: radial-gradient(ellipse at 50% 70%, #f07a4a 0%, #8a3a4a 18%, #27355a 45%, var(--navy) 100%);
  }

  h2 {
    position: absolute; left: 26px;
    font-weight: 800; font-size: 22px; letter-spacing: 0.6px;
    color: var(--blue-bright); line-height: 24px;
  }
  .body-text { position: absolute; left: 27px; font-size: 9.6px; line-height: 10px; }
  .lead-text { position: absolute; left: 27px; font-size: 13px; line-height: 12.8px; }
  .quote { position: absolute; font-weight: 700; color: var(--blue-bright); }
  .quote-lg { font-size: 13px; line-height: 15.5px; left: 27px; }
  .quote-sm { font-size: 9.5px; line-height: 11.5px; font-weight: 600; }
  .attrib { position: absolute; font-size: 8.3px; }
  .attrib b { font-weight: 700; }
  .bullets { position: absolute; list-style: none; font-size: 8.6px; line-height: 9.2px; }
  .bullets li { margin-bottom: 9px; }
  .bullets li::before { content: "• "; }
  .bullets b { font-weight: 700; }

  .footer-band {
    left: 0; top: 1115px; width: 315px; height: 53px; background: var(--blue-deep);
  }
  .footer-email {
    left: 0; top: 1115px; width: 315px; height: 53px;
    display: flex; align-items: center; justify-content: center;
    color: var(--white); font-size: 15.5px; font-weight: 600;
  }
  .footer-panel {
    left: 315px; top: 1095px; width: 533px; height: 92px;
    background: linear-gradient(90deg, var(--blue-pale) 0%, #6cc6ff 55%, #3f9bff 100%);
  }
  .footer-tagline {
    left: 339px; top: 1117px; width: 500px;
    color: var(--white); font-size: 22.5px; line-height: 23px; font-weight: 600;
  }
</style>
</head>
<body>
  <div class="abs brand-card"></div>
  <div class="abs brand-name"><div class="mark"></div><span>HARBORLINE<br>COVERAGE GROUP</span></div>

  <div class="abs photo-top" role="img" aria-label="Photo of a hand drawing home, education, family and car icons on a glass panel"></div>
  <div class="abs headline-box"></div>
  <h1 class="abs headline">We provide value every step of the way, at no additional cost!</h1>

  <svg class="abs fold" width="101" height="113" viewBox="0 0 101 113" aria-hidden="true">
    <polygon points="0,0 101,0 101,113" fill="#1657d4"/>
  </svg>
  <div class="abs photo-main" role="img" aria-label="Photo of an open hand holding a glowing shield with family, home, car, medical kit and savings icons"></div>

  <h2 style="top:313px">OUR SERVICES</h2>
  <p class="body-text" style="top:340px;width:290px">As a BGA, our mission is to connect agents and advisors with insurance carriers and help our customers find the correct product that meets each client’s needs. From our experienced Point of Sale Strategists to our professional Concierge Service Team, we provide value every step of the way, at no additional cost!</p>
  <p class="quote quote-lg" style="top:408px;width:310px">“From quote to issue and review to service, each case is an opportunity of quality care. “</p>
  <p class="attrib" style="left:27px;top:450px"><b>Dana K,</b> New Business Specialist</p>

  <h2 style="top:483px">OUR POINT OF SALE STRATEGISTS</h2>
  <p class="body-text" style="top:510px;width:370px">work directly with agents and advisors to provide experienced assistance for immediate client needs, as well as maximizing insurance planning to find opportunities for all clients.</p>
  <ul class="bullets" style="left:27px;top:557px;width:345px">
    <li><b>Dedicated Strategists</b> – We develop a personal relationship with each advisor, giving you confidence that we are working in your best interest. Always here to help with quotes and analysis.</li>
    <li><b>Quotes Made Easy</b> - Access our online system or simply email your specialist to receive quotes for your client reviews, life event circumstances, estate needs, or prospect meetings.</li>
    <li><b>National Footprint</b> – Our team is nationwide, allowing us to serve you regardless of location, time zone, or licensing limitations.</li>
  </ul>

  <h2 style="top:688px">OUR CONCIERGE SERVICE TEAM</h2>
  <p class="lead-text" style="top:716px;width:360px">is comprised of several specialists. Once an agent moves forward with an application, simply hand it off to our staff, ensuring your policy is processed accurately and delivered in a timely manner.</p>
  <p class="quote quote-lg" style="top:780px;width:340px">“We are the go-to-person for anything the agent needs; we handle everything from A to Z!”</p>
  <p class="attrib" style="left:27px;top:822px"><b>Rita M,</b> Application Specialist/Case Manager</p>

  <ul class="bullets" style="left:27px;top:856px;width:395px">
    <li><b>Dedicated Case Managers</b> – Your personal case manager gives us a better understanding of your business, expectations, and preferred process.</li>
    <li><b>Carrier Familiarity</b> – Our experience enables us to provide correct forms from the get-go, as well as properly relay carrier specific processes and manage expectations.</li>
    <li><b>Agent Licensing</b> – We confirm you are correcty licensed and appointed before applications are initiated. If appointment is needed, we help you get this done in a timely, technology efficient manner.</li>
    <li><b>No Hassle Paperwork</b> – Our team will handle all application and underwriting needs, assuring a efficient process and less hassle for the agent.</li>
    <li><b>No Fluff Process</b> – We create a seamless process by gathering what is required for underwriting, eliminating the unnecessary back and forth with clients that often delays the policy and annoys clients.</li>
  </ul>
  <p class="quote quote-sm" style="left:27px;top:1013px;width:395px">“Oftentimes clients can be uncomfortable disclosing personal health history to their advisor, but will answer freely with someone in my role. I let clients know we have their best interest at heart.”</p>
  <p class="attrib" style="left:27px;top:1051px"><b>Marisa T,</b> Application Specialist</p>

  <ul class="bullets" style="left:431px;top:818px;width:395px">
    <li><b>Client Confidentiality</b> – Our application specialist contacts the client and takes the application, eliminating the need for clients to share personal medical information with their advisor.</li>
    <li><b>Proactive Approach</b> – We proactively order medical records and exams for most cases, speeding up the UW process by days if not weeks, resulting in quicker decisions.</li>
    <li><b>Electronic Signatures</b> –By leveraging technology, we will utilize electronic signature capabilities for both agent and client, speeding up the overall process.</li>
  </ul>
  <p class="quote quote-sm" style="left:428px;top:918px;width:400px">“Our weekly updates keep advisors well informed throughout the process.”</p>
  <p class="attrib" style="left:428px;top:937px"><b>Joanna P,</b> Senior Case Manager</p>
  <ul class="bullets" style="left:431px;top:969px;width:395px">
    <li><b>Recurring Updates</b> – Your case manager will keep you updated on the status of all cases.</li>
    <li><b>Online Case Tracker</b> – This tool allows you to access the status of your cases. All carriers. All cases. All the time.</li>
    <li><b>Policy Delivery</b> – we ensure premiums are paid and policy documents are delivered.</li>
  </ul>

  <svg class="abs" style="left:295px;top:1095px" width="20" height="92" viewBox="0 0 20 92" aria-hidden="true">
    <polygon points="20,0 20,20 8,20" fill="#1657d4"/>
    <polygon points="20,92 20,73 0,73" fill="#0e3fa8"/>
  </svg>
  <div class="abs footer-band"></div>
  <div class="abs footer-panel"></div>
  <p class="abs footer-email">contact@harborline-coverage.com</p>
  <p class="abs footer-tagline">We look forward to using our expertise to help you grow your business.</p>
</body>
</html>
```